20 year old business card needs re-design

We need to redesign our corporate business card look. We need something that appears more modern, eye catchy but professional.

Target Market(s)

manufacturing industry

Industry/Entity Type

Manufacturer

Contact Information for Business Card

One side can have the logo. Other side can have contact information.

Font styles to use
Serif

Colors
3277b5
33b8a4
ffffff

Requirements
Must have
• Eye catchy - need to standout from the crowd. company logo cannot change. Full name, job title, phone number and email address.
Should not have
• Fax, business address is not necessary.

```html
<!DOCTYPE html>
<html lang="en">
<head>
<meta charset="utf-8">
<title>Norvale Industrial – Business Card</title>
<link rel="stylesheet" href="https://fonts.googleapis.com/css2?family=Oswald:wght@500&family=Work+Sans:wght@400;700&display=swap">
<style>
  :root {
    --bg: #1a1a1a;
    --card: #262626;
    --card-edge: #2e2e2e;
    --blue: #3277b5;
    --teal: #33b8a4;
    --white: #ffffff;
  }
  * { margin: 0; padding: 0; box-sizing: border-box; }
  html, body { width: 1200px; height: 900px; overflow: hidden; }
  body {
    background: var(--bg);
    font-family: "Work Sans", Arial, sans-serif;
    color: var(--white);
    position: relative;
  }
  .card {
    position: absolute;
    left: 250px;
    width: 700px;
    height: 400px;
    background: linear-gradient(160deg, var(--card) 0%, var(--card-edge) 100%);
    border-bottom: 9px solid var(--blue);
    box-shadow: 0 12px 30px rgba(0,0,0,.5);
  }
  .card--front { top: 30px; }
  .card--back { top: 470px; }

  .brand {
    position: absolute;
    top: 140px;
    left: 0; right: 0;
    display: flex;
    align-items: center;
    justify-content: center;
    gap: 16px;
  }
  .brand__mark {
    width: 34px; height: 34px;
    background: var(--blue);
  }
  .brand__name {
    font-weight: 700;
    font-size: 46px;
    letter-spacing: -0.5px;
    color: var(--white);
  }
  .front__url {
    position: absolute;
    bottom: 22px;
    left: 0; right: 0;
    text-align: center;
    font-size: 15px;
    letter-spacing: 2.5px;
  }

  .back__layout {
    position: absolute;
    top: 150px;
    left: 70px;
    display: flex;
    align-items: center;
  }
  .person { text-align: right; padding-right: 26px; }
  .person__name {
    font-family: "Oswald", "Arial Narrow", sans-serif;
    font-weight: 500;
    font-size: 40px;
    letter-spacing: 1.5px;
    color: var(--blue);
    line-height: 1.05;
    text-transform: uppercase;
  }
  .person__title { font-size: 19px; margin-top: 2px; }
  .divider {
    width: 2px; height: 72px;
    background: var(--teal);
  }
  .contact { list-style: none; padding-left: 26px; }
  .contact__item {
    display: flex; align-items: center; gap: 14px;
    font-size: 19px; letter-spacing: .8px; line-height: 1.35;
  }
  .contact__icon { width: 15px; height: 15px; flex: none; }
</style>
</head>
<body>
  <section class="card card--front">
    <div class="brand">
      <span class="brand__mark"></span>
      <span class="brand__name">Norvale Industrial</span>
    </div>
    <p class="front__url">norvaleindustrial.com</p>
  </section>

  <section class="card card--back">
    <div class="back__layout">
      <div class="person">
        <h1 class="person__name">Dana Merrow</h1>
        <p class="person__title">Senior Project Manager</p>
      </div>
      <span class="divider"></span>
      <ul class="contact">
        <li class="contact__item">
          <svg class="contact__icon" viewBox="0 0 16 16"><rect x="4" y="1" width="8" height="14" rx="1.5" fill="none" stroke="#3277b5" stroke-width="1.6"/><circle cx="8" cy="12.3" r=".9" fill="#3277b5"/></svg>
          555-014-2200 xt 104
        </li>
        <li class="contact__item">
          <svg class="contact__icon" viewBox="0 0 16 16"><rect x="1" y="3" width="14" height="10" fill="#3277b5"/><path d="M1 3.5 8 9l7-5.5" fill="none" stroke="#262626" stroke-width="1.3"/></svg>
          dana@norvaleindustrial.com
        </li>
        <li class="contact__item">
          <svg class="contact__icon" viewBox="0 0 16 16"><circle cx="6.5" cy="6.5" r="4.5" fill="none" stroke="#3277b5" stroke-width="2"/><path d="M10 10l4.5 4.5" stroke="#3277b5" stroke-width="2.2" stroke-linecap="round"/></svg>
          NorvaleIndustrial.com
        </li>
      </ul>
    </div>
  </section>
</body>
</html>
```